Valdane Companies Business Card Design

We need a new business card for our Private Equity Real Estate Development firm, “Valdane” and our EB-5 regional center “Thornmere Regional Center” on one card. We prefer a design that is simple, elegant, and represents the luxury products we design and build as well as the financial security and stability our successful history has produced. We are an industry leader in our field and 3rd generation family business that has evolved into an institutional quality investment platform. Considered design size is standard business card dimensions (3.5 x 2 inches with an additional 1/8 inch space for design elements or backgrounds that extend beyond the finished size of your piece.

Target Market(s)

• High net worth individuals
• Highly skilled technical workers and physicians in the US seeking investment-based immigration opportunities
• Sophisticated private equity investors
• Intermediary partners include domestic attorneys and investment brokers, as well as international agent networks
• US real estate developers

Industry/Entity Type

Finance

Contact Information for Business Card

(Providing placeholder info for personal information, please design for longer character spaces, longer names and addresses etc..)
• Logo for Valdane
• Logo for Thornmere Regional Center
• Full name: Marcus Valdane
• Job title: CEO
• Email address: mvaldane@valdanecompanies.com
• Cell phone number: +1.555.314.2287
• Office number +1.555.628.4410
• Office address: Larkfield Court 5, 4817 Vista Orilla, San Ramon, CA.
• Website: www.valdanecompanies.com

Font styles to use
Serif
Sans Serif

Colors
ec1f27
ffffff
000000

Requirements
Must have
• • Logo for Valdane
• • Logo for Thornmere Regional Center
• - Use rounded corners
• (See .ai file included for logos)
Nice to have
• • Simple, elegant design
• • Aesthetically compatible with our website design (www.valdanecompanies.com)
• • Color palette including but not limited to white, black, and red (as per logos)
Should not have
• - Not too much red color
• - Do not stack both logos on top of each other

```html
<!DOCTYPE html>
<html lang="en">
<head>
<meta charset="UTF-8">
<title>Valdane Companies – Business Card</title>
<link rel="stylesheet" href="https://fonts.googleapis.com/css2?family=Lato:wght@400;700&display=swap">
<style>
  :root {
    --backdrop: #1f1f1f;
    --card: #151515;
    --red: #ec1f27;
    --deep-red: #a8182a;
    --white: #ffffff;
    --muted: #d9d9d9;
  }
  * { box-sizing: border-box; margin: 0; padding: 0; }
  html, body {
    width: 1200px; height: 900px; overflow: hidden;
    background: var(--backdrop);
    font-family: "Lato", Arial, sans-serif;
  }
  .stage { position: relative; width: 1200px; height: 900px; }
  .card {
    position: absolute; left: 285px; width: 630px; height: 360px;
    background: var(--card); border-radius: 14px;
    box-shadow: 0 10px 30px rgba(0,0,0,.45);
    overflow: hidden;
  }
  .card--front { top: 60px; display: flex; align-items: center; justify-content: center; }
  .card--back { top: 470px; }

  .brand { display: flex; align-items: center; gap: 14px; color: var(--deep-red); }
  .brand__mark { width: 16px; height: 16px; background: var(--deep-red); }
  .brand__name {
    font-weight: 700; text-transform: uppercase; letter-spacing: 3px;
    font-size: 26px;
  }
  .card--back .brand { position: absolute; left: 40px; top: 36px; gap: 10px; }
  .card--back .brand__mark { width: 11px; height: 11px; }
  .card--back .brand__name { font-size: 15px; letter-spacing: 2px; }

  .person { position: absolute; left: 40px; top: 92px; }
  .person__name { color: var(--red); font-size: 29px; font-weight: 400; text-transform: uppercase; letter-spacing: .5px; }
  .person__title { color: var(--white); font-size: 15px; margin-top: 2px; }

  .address { position: absolute; left: 40px; top: 168px; color: var(--white); font-size: 15px; line-height: 1.35; }

  .contacts { position: absolute; left: 40px; top: 228px; list-style: none; color: var(--white); font-size: 16px; }
  .contacts li { display: flex; align-items: center; gap: 10px; height: 24px; }
  .contacts svg { width: 12px; height: 12px; flex: none; }
  .contacts .accent { color: var(--red); }

  .mark-area {
    position: absolute; right: 50px; top: 55px; width: 250px; height: 250px;
    background: linear-gradient(135deg, #c4243f 0%, #8f1428 60%, #5e0c1b 100%);
  }
</style>
</head>
<body>
<main class="stage">
  <section class="card card--front" aria-label="Card front">
    <div class="brand">
      <span class="brand__mark"></span>
      <span class="brand__name">Thornmere Regional Center</span>
    </div>
  </section>

  <section class="card card--back" aria-label="Card back">
    <div class="brand">
      <span class="brand__mark"></span>
      <span class="brand__name">Thornmere Regional Center</span>
    </div>

    <div class="person">
      <h1 class="person__name">Marcus Valdane</h1>
      <p class="person__title">CEO</p>
    </div>

    <p class="address">Larkfield Court 5, 4817 Vista<br>Orilla, San Ramon, CA.</p>

    <ul class="contacts">
      <li>
        <svg viewBox="0 0 12 12"><path fill="#ec1f27" d="M3 1l2 2.5-1.2 1.2a6 6 0 0 0 3.5 3.5L8.5 7 11 9l-1.5 2C5 11 1 7 1 2.5z"/></svg>
        +1.555.314.2287
      </li>
      <li>
        <svg viewBox="0 0 12 12"><rect x="3" y="0.5" width="6" height="11" rx="1.2" fill="#ec1f27"/><rect x="4" y="2" width="4" height="7" fill="#151515"/></svg>
        +1.555.628.4410
      </li>
      <li>
        <svg viewBox="0 0 12 12"><rect x="0.5" y="2" width="11" height="8" fill="none" stroke="#ec1f27" stroke-width="1.2"/><path d="M1 2.5l5 4 5-4" fill="none" stroke="#ec1f27" stroke-width="1.2"/></svg>
        mvaldane@valdanecompanies.com
      </li>
      <li>
        <svg viewBox="0 0 12 12"><circle cx="6" cy="6" r="5" fill="none" stroke="#ec1f27" stroke-width="1.2"/><path d="M1 6h10M6 1c-2.5 3-2.5 7 0 10M6 1c2.5 3 2.5 7 0 10" fill="none" stroke="#ec1f27" stroke-width="1"/></svg>
        <span>www.<span class="accent">valdanecompanies</span>.com</span>
      </li>
    </ul>

    <div class="mark-area" role="img" aria-label="Large brand symbol area in deep red"></div>
  </section>
</main>
</body>
</html>
```